Venture Capital firm needs modern business cards

We are a Venture Capital firm within financial services/Asset management. The industry generally has basic business cards with black, blue and maybe green/yellow design elements.
Our firm has a four-colour swoosh logo. We are based in London and want to stand out, just a little bit!, from the crowd. Our company is called LORV Investments and the 'C' stands for collaboration thus using makerswarm is a natural portal for our business card design competition. Our logo came via makerswarm too!
We use 'Venture Partner in Asset Management' as our tagline and this is Trademark registered. We operate in a conservative industry and we should not overstep our mark. The logo is colorful as it is and therefore the rest of the design should not be too fanciful.
The objective is twofold: make our logo element stick and memorable with our audience, whilst representing a conservative yet young image.
Updates
The Business Card obviously needs a field for Name, Surname, Job Title, Adress fields: Street, City, Postcode, Country, telefone and cell number, website address, etc.
We have uploaded the ai file. We trust that these are OK. If not, please advise.
Reason: We have have been busy with a client engagement. We will set the project as Guaranteed in return for the troubles we cause. Apologies for the confusion.
Thank you all for these great and creative design suggestions. The team is very happy with a number of your ideas! We will be in touch tomorrow to give individual feedback before the project closes on Friday. We look forward to working with some of you to narrow down your creations. Thank you, LORV Investments team.
All,
Target Market(s)
Financial Services Professionals, Investors, Media, 35-70 years, mainly male, well educated
Industry/Entity Type
Conservative
Requirements
Must have
- We must make use of our logo and potential tagline 'Venture Partner in Asset Management' as we are establishing a new Brand and new company in the market.
We can use 'LORV', 'LORV Investments', and 'LORV Investments'+tagline 'Venture Partner in Asset Management' or simply the four-colour swoosh plus the name of the company as part of the text. (see files)
All design elements are available in black or grey-scale if required. (grey scale swoosh attached).
Due to regulation we must have the following wording on the card in small print 'LORV Investments is an Appointed Representative of Bramwell Holdings Partnership Limited, which is authorised by the Monetary Oversight Board'.
Nice to have
- We would consider designs that make use of different printing techniques such embossing/debossing, UV spot etc.
We attach our colour palette in the files section for your reference.
Should not have
- The font we use for our company name is 'EXO' so do not use a font style that clashes with the corporate fonts, please.
Do not use other design elements than the ones we provide in the file library as part of this project.

```html
<!DOCTYPE html>
<html lang="en">
<head>
<meta charset="utf-8">
<title>LORV Investments – Business Cards</title>
<link rel="stylesheet" href="https://fonts.googleapis.com/css2?family=Arimo:wght@400;700&display=swap">
<style>
  :root {
    --stage: #e6e7e9;
    --card-white: #f1f2f4;
    --card-blue: #88cfd3;
    --card-yellow: #f9d10b;
    --ink-light: #ffffff;
    --ink-grey: #4a4a4a;
    --brand-grey: #b9babd;
    --shadow: 0 3px 5px rgba(0,0,0,0.18);
  }
  * { margin: 0; padding: 0; box-sizing: border-box; }
  html, body { width: 1200px; height: 800px; overflow: hidden; }
  body {
    background: var(--stage);
    font-family: "Arimo", Arial, sans-serif;
    position: relative;
  }
  .card {
    position: absolute;
    width: 388px;
    height: 222px;
    border-radius: 12px;
    box-shadow: var(--shadow);
    overflow: hidden;
  }
  .card--blue   { left: 96px;  top: 70px;  background: var(--card-blue); }
  .card--back-a { left: 514px; top: 70px;  background: var(--card-white); }
  .card--back-b { left: 96px;  top: 535px; background: var(--card-white); }
  .card--yellow { left: 514px; top: 535px; background: var(--card-yellow); }

  /* Front side: card holder */
  .holder {
    position: absolute;
    right: 18px;
    top: 62px;
    text-align: right;
    color: var(--ink-light);
    white-space: nowrap;
  }
  .holder__name { font-weight: 700; font-size: 14px; line-height: 16px; }
  .holder__role { font-size: 11px; line-height: 14px; }

  /* Front side: contact rows, text right-aligned, icon column to the right */
  .contact {
    position: absolute;
    right: 171px;
    color: var(--ink-light);
    font-size: 11.5px;
    line-height: 15px;
    text-align: right;
    white-space: nowrap;
  }
  .contact--email   { top: 62px; }
  .contact--phone   { top: 81px; }
  .contact--mobile  { top: 100px; }
  .contact--address { top: 115px; }

  .icon {
    position: absolute;
    right: 144px;
    width: 14px;
    height: 14px;
  }
  .icon--email   { top: 63px; }
  .icon--phone   { top: 82px; }
  .icon--mobile  { top: 101px; }
  .icon--address { top: 124px; }

  .disclaimer {
    position: absolute;
    right: 147px;
    top: 148px;
    width: 190px;
    color: var(--ink-light);
    font-size: 6.5px;
    line-height: 8px;
    text-align: right;
  }

  .brand {
    position: absolute;
    display: flex;
    align-items: center;
    gap: 6px;
    font-size: 11px;
    font-weight: 700;
    white-space: nowrap;
  }
  .brand__dot { width: 12px; height: 12px; border-radius: 50%; }
  .card--blue .brand,
  .card--yellow .brand { right: 18px; bottom: 28px; color: var(--ink-light); }
  .card--blue .brand__dot,
  .card--yellow .brand__dot { background: var(--ink-light); }

  /* Back side */
  .website {
    position: absolute;
    right: 12px;
    top: 15px;
    font-size: 11.5px;
    color: var(--ink-grey);
  }
  .card--back-a .brand,
  .card--back-b .brand { left: 22px; bottom: 28px; color: var(--brand-grey); }
  .card--back-a .brand__dot,
  .card--back-b .brand__dot { background: #c9cacc; }

  .note {
    position: absolute;
    left: 782px;
    top: 474px;
    font-size: 14px;
    color: #222;
  }
</style>
</head>
<body>

<section class="card card--blue" aria-label="Front of card, blue option">
  <div class="holder">
    <p class="holder__name">Daniel Harrow</p>
    <p class="holder__role">Chairman</p>
  </div>
  <p class="contact contact--email">daniel@lorvinvestments.com</p>
  <p class="contact contact--phone">+1 (800) 555-0147</p>
  <p class="contact contact--mobile">+1 (800) 555-0147</p>
  <p class="contact contact--address">12 Harbour Lane, 40 Carrow Square,<br>London, United Kingdom EC4N 2QA</p>
  <svg class="icon icon--email" viewBox="0 0 14 14" fill="none" stroke="#fff" stroke-width="1"><rect x="1" y="3" width="12" height="8"/><path d="M1 3l6 5 6-5"/></svg>
  <svg class="icon icon--phone" viewBox="0 0 14 14" fill="none" stroke="#fff" stroke-width="1"><path d="M3 1.5l2 2.5-1 1.5c1 2 2.5 3.5 4.5 4.5l1.5-1 2.5 2-1 1.5C7 12 2 7 1.5 2.5z"/></svg>
  <svg class="icon icon--mobile" viewBox="0 0 14 14" fill="none" stroke="#fff" stroke-width="1"><rect x="4" y="1" width="6" height="12" rx="1"/><path d="M6 11h2"/></svg>
  <svg class="icon icon--address" viewBox="0 0 14 14" fill="none" stroke="#fff" stroke-width="1"><path d="M1.5 7L7 2l5.5 5M3 6v6.5h8V6M6 12.5V9h2v3.5"/></svg>
  <p class="disclaimer">'LORV Investments is an Appointed Representative of Bramwell Holdings Partnership Limited, which is authorised by the Monetary Oversight Board'.</p>
  <div class="brand"><span class="brand__dot"></span>LORV Investments</div>
</section>

<section class="card card--back-a" aria-label="Back of card, white">
  <p class="website">www.lorvinvestments.com</p>
  <div class="brand"><span class="brand__dot"></span>LORV Investments</div>
</section>

<section class="card card--back-b" aria-label="Back of card, white">
  <p class="website">www.lorvinvestments.com</p>
  <div class="brand"><span class="brand__dot"></span>LORV Investments</div>
</section>

<section class="card card--yellow" aria-label="Front of card, yellow option">
  <div class="holder">
    <p class="holder__name">Daniel Harrow</p>
    <p class="holder__role">Chairman</p>
  </div>
  <p class="contact contact--email">daniel@lorvinvestments.com</p>
  <p class="contact contact--phone">+1 (800) 555-0147</p>
  <p class="contact contact--mobile">+1 (800) 555-0147</p>
  <p class="contact contact--address">12 Harbour Lane, 40 Carrow Square,<br>London, United Kingdom EC4N 2QA</p>
  <svg class="icon icon--email" viewBox="0 0 14 14" fill="none" stroke="#fff" stroke-width="1"><rect x="1" y="3" width="12" height="8"/><path d="M1 3l6 5 6-5"/></svg>
  <svg class="icon icon--phone" viewBox="0 0 14 14" fill="none" stroke="#fff" stroke-width="1"><path d="M3 1.5l2 2.5-1 1.5c1 2 2.5 3.5 4.5 4.5l1.5-1 2.5 2-1 1.5C7 12 2 7 1.5 2.5z"/></svg>
  <svg class="icon icon--mobile" viewBox="0 0 14 14" fill="none" stroke="#fff" stroke-width="1"><rect x="4" y="1" width="6" height="12" rx="1"/><path d="M6 11h2"/></svg>
  <svg class="icon icon--address" viewBox="0 0 14 14" fill="none" stroke="#fff" stroke-width="1"><path d="M1.5 7L7 2l5.5 5M3 6v6.5h8V6M6 12.5V9h2v3.5"/></svg>
  <p class="disclaimer">'LORV Investments is an Appointed Representative of Bramwell Holdings Partnership Limited, which is authorised by the Monetary Oversight Board'.</p>
  <div class="brand"><span class="brand__dot"></span>LORV Investments</div>
</section>

<p class="note">• Note : These are two colour options,&nbsp; swoosh is die cut.</p>

</body>
</html>
```